VELQUINT

1. My company will allow people to buy either stock made or custom scented aromatherapy candles, lotions,soaps,body sprays, and wax melts. As there isn't a company that allows for custom oil scent mixes but me. We are just starting with the candles and the other items will be coming later.

2. My target audience is anyone who would want to buy my product. It isn't really limited due to the nature of the product I will be providing.

3. velquint.com is the domain name (purchased from plorvex.com).

4. So what I really need is the shopping cart function. A fully coded shopping cart that will calculate shipping and sales tax if need be. I need the cart function to be just like every other major retailers shopping cart function. So they can click on an item they want and have it go into a shopping cart for the customer to then be able to go and pay for their goods. I also need help creating single pages for each product. So that each thing we make has a separate page with a description and an add to cart button.

5. I would like the color scheme to follow the logo I made. I would also like the logo top center of first page. I would like the quote " elevate your choices in aromatherapy products"

^. I basically need a checkout just like every other good website. A clear shipping area for them to populate, sales tax calculator, ya know everything a normal checkout has like tressly or dunvexa.com. I also have a vonk account already as well.

```html
<!DOCTYPE html>
<html lang="en">
<head>
<meta charset="utf-8">
<title>VELQUINT — Aromatherapy Products</title>
<link rel="stylesheet" href="https://fonts.googleapis.com/css2?family=Jost:wght@400;500&family=Roboto:wght@400;500;700&display=swap">
<style>
:root{
  --black:#000;
  --ink:#0a0a0a;
  --white:#fff;
  --purple:#9a58dc;
  --purple-deep:#4b2bc4;
  --blue:#3f9cf0;
  --grad:linear-gradient(90deg,#a95bdc,#5a8ef0);
  --card-line:#4a2f73;
  --star:#f0a417;
  --muted:#555;
}
*{margin:0;padding:0;box-sizing:border-box}
html,body{width:1200px;height:3845px;overflow:hidden;background:var(--black)}
body{position:relative;font-family:"Roboto",sans-serif;color:var(--white)}
.abs{position:absolute}
.display{font-family:"Jost",sans-serif;font-weight:400;letter-spacing:.5px}

/* top bar */
.topbar{left:0;top:0;width:1200px;height:46px;background:var(--purple-deep);}
.topbar-note{left:0;width:1200px;top:15px;text-align:center;font-size:13px;font-weight:500}
.topbar .soc{top:7px;width:33px;height:33px;border:1.5px solid #fff;border-radius:50%}

/* header */
.header{left:0;top:46px;width:1200px;height:133px;background:var(--black)}
.nav a{position:absolute;top:57px;font-size:13px;color:#fff;text-decoration:none;font-weight:500}
.nav a.active{color:var(--purple);text-decoration:underline}
.btn{display:flex;align-items:center;justify-content:center;gap:12px;border-radius:26px;background:var(--grad);color:#fff;font-weight:700;font-size:14px}
.btn .chev{width:20px;height:20px;border-radius:50%;background:#fff;display:flex;align-items:center;justify-content:center}
.logo-tab{left:511px;top:50px;width:178px;height:178px;border-radius:50%;background:var(--black);z-index:5;display:flex;align-items:center;justify-content:center;gap:6px}
.wordmark{font-family:"Jost",sans-serif;font-weight:500;font-size:22px;color:#9a7ae8;letter-spacing:2px}
.wordmark-dot{width:12px;height:12px;border-radius:50%;background:#9a7ae8}

/* hero */
.hero-photo{left:0;top:179px;width:1200px;height:700px;background:linear-gradient(110deg,#c9bdb2 0%,#e6e1dc 35%,#d8d0c8 60%,#8f7d6e 100%)}
.hero-box{left:249px;top:351px;width:702px;height:309px;background:rgba(255,255,255,.55);text-align:center;color:#111}
.hero-box h1{font-size:46px;line-height:54px;margin-top:26px;color:#111}
.bar{width:50px;height:3px;background:var(--purple);margin:0 auto}
.hero-box p{font-size:16.5px;line-height:27px;margin-top:22px}
.arrow-dot{width:36px;height:36px;border-radius:50%;background:#fff;display:flex;align-items:center;justify-content:center}

/* section titles */
.sec-title{left:0;width:1200px;text-align:center;font-size:46px}

/* categories */
.cat{width:221px;text-align:center}
.cat-ring{width:221px;height:221px;border-radius:50%;padding:3px;background:linear-gradient(160deg,#9a58dc,#3f9cf0)}
.cat-photo{width:100%;height:100%;border-radius:50%}
.cat-icon{position:absolute;left:72px;top:175px;width:78px;height:78px;border-radius:50%;background:linear-gradient(160deg,#a95bdc,#6d6ff0);display:flex;align-items:center;justify-content:center}
.cat-name{margin-top:56px;font-size:18px;font-weight:700;line-height:30px}
.dots span{display:inline-block;width:17px;height:17px;border:1.5px solid #fff;border-radius:50%;margin:0 4px}
.dots span.on{background:var(--purple);border-color:var(--purple)}

/* featured */
.featured{left:0;top:1519px;width:1200px;height:669px;background:var(--ink)}
.feat-photo{left:43px;top:1598px;width:351px;height:514px;border-radius:30px;background:linear-gradient(160deg,#7b8a70,#c3a27f 55%,#7b6a55)}
.tab{height:39px;border:1.5px solid #aaa;border-radius:20px;display:flex;align-items:center;justify-content:center;gap:10px;font-size:10.5px;font-weight:700}
.tab.on{background:var(--grad);border-color:transparent}
.tab .chev{width:15px;height:15px;border-radius:50%;background:#fff}
.pcard{border:1.5px solid var(--card-line);border-radius:12px;text-align:center;background:var(--black)}
.pcard.hl{border:2.5px solid #6a8ef0}
.pcard .ph{margin:5px;height:183px;border-radius:10px}
.pcard .cart{position:absolute;right:14px;top:14px;width:26px;height:26px;border-radius:50%;background:#ddd}
.pcard.hl .cart{background:#7a6ff0}
.pcard h3{font-size:16.5px;font-weight:700;margin-top:18px}
.rating{font-size:8px;margin-top:6px;color:#ccc}
.rating b{color:var(--star);letter-spacing:1px;font-size:9px}
.price{font-size:17px;font-weight:700;margin-top:9px}
.nav-pair .l,.nav-pair .r{width:36px;height:36px;border-radius:50%;display:flex;align-items:center;justify-content:center}
.nav-pair .l{border:1.5px solid #fff}
.nav-pair .r{background:linear-gradient(160deg,#a95bdc,#4a8ff0)}

/* testimonials */
.clients{left:0;top:2188px;width:1200px;height:552px;background:linear-gradient(100deg,#a8bcb4 0%,#d9dcd6 40%,#e8e6e1 60%,#b9bfa8 100%)}
.tcard{width:308px;height:283px;background:#fff;border-radius:30px 30px 0 0;color:#333;padding:26px 26px 0}
.tcard .qmark{position:absolute;left:22px;top:12px;font-family:"Jost",sans-serif;font-size:60px;color:#ddd;line-height:1}
.tcard p{position:relative;font-size:14.5px;line-height:26.5px;text-align:justify}
.person{display:flex;align-items:center;gap:16px;margin-top:20px}
.avatar{width:60px;height:60px;border-radius:50%;background:linear-gradient(160deg,#d8c1ab,#8b6a54)}
.person b{display:block;font-size:16px;color:#111}
.person i{font-style:normal;color:var(--star);font-size:11px;letter-spacing:2px}

/* footer */
.fhead{font-size:16.5px;font-weight:700}
.flink{display:flex;align-items:center;gap:15px;font-size:14px}
.fchev{width:14px;height:14px;border-radius:50%;background:var(--purple)}
.cicon{width:38px;height:38px;border-radius:50%;background:#fff;display:flex;align-items:center;justify-content:center}
.fsoc{width:36px;height:36px;border:1.5px solid #fff;border-radius:50%}
</style>
</head>
<body>

<!-- top bar -->
<div class="abs topbar">
  <div class="abs topbar-note">ABOVE BUY $99 SHIPPING FREE</div>
  <div class="abs soc" style="left:938px" aria-label="Social link"></div>
  <div class="abs soc" style="left:977px" aria-label="Social link"></div>
  <div class="abs soc" style="left:1016px" aria-label="Social link"></div>
  <div class="abs soc" style="left:1054px" aria-label="Social link"></div>
</div>

<!-- header -->
<header class="abs header">
  <nav class="nav">
    <a class="active" style="left:110px">HOME</a>
    <a style="left:178px">ABOUT US</a>
    <a style="left:270px">OUR PRODUCTS</a>
    <a style="left:397px">BLOG</a>
  </nav>
  <div class="abs btn" style="left:788px;top:41px;width:160px;height:47px">CONTACT US <span class="chev"><svg width="8" height="10" viewBox="0 0 8 10"><path d="M2 1l4 4-4 4" stroke="#7a5ce8" stroke-width="2" fill="none"/></svg></span></div>
  <svg class="abs" style="left:980px;top:56px" width="16" height="16" viewBox="0 0 16 16"><circle cx="6.5" cy="6.5" r="4.5" stroke="#fff" stroke-width="2" fill="none"/><path d="M10 10l4 4" stroke="#fff" stroke-width="2.4"/></svg>
  <svg class="abs" style="left:1018px;top:56px" width="14" height="15" viewBox="0 0 14 15"><circle cx="7" cy="4" r="3.6" fill="#fff"/><path d="M0 15c0-5 3-7 7-7s7 2 7 7z" fill="#fff"/></svg>
  <svg class="abs" style="left:1054px;top:57px" width="16" height="14" viewBox="0 0 16 14"><path d="M0 1h3l2 8h9l2-6H4" stroke="#fff" stroke-width="2" fill="none"/><circle cx="6" cy="12" r="1.6" fill="#fff"/><circle cx="13" cy="12" r="1.6" fill="#fff"/></svg>
  <span class="abs" style="left:1072px;top:57px;font-size:13px;color:var(--purple)">(0)</span>
</header>
<div class="abs logo-tab"><span class="wordmark-dot"></span><span class="wordmark">VELQUINT</span></div>

<!-- hero -->
<div class="abs hero-photo" role="img" aria-label="Woman in a white robe holding a dropper bottle of essential oil beside lavender and amber bottles"></div>
<div class="abs hero-box">
  <h1 class="display">ELEVATE YOUR CHOICES<br>IN AROMATHERAPY PRODUCTS</h1>
  <div class="bar" style="margin-top:4px"></div>
  <p>Lorem ipsum dolor sit amet, consectetur adipiscing elit, sed do eiusmod<br>tempor incididunt ut labore et dolorea.</p>
  <div class="btn" style="width:151px;height:46px;margin:20px auto 0">SHOP NOW <span class="chev"><svg width="8" height="10" viewBox="0 0 8 10"><path d="M2 1l4 4-4 4" stroke="#7a5ce8" stroke-width="2" fill="none"/></svg></span></div>
</div>
<div class="abs arrow-dot" style="left:42px;top:437px"><svg width="10" height="14" viewBox="0 0 10 14"><path d="M7 2L2 7l5 5" stroke="#000" stroke-width="2.5" fill="none"/></svg></div>
<div class="abs arrow-dot" style="left:1120px;top:437px"><svg width="10" height="14" viewBox="0 0 10 14"><path d="M3 2l5 5-5 5" stroke="#000" stroke-width="2.5" fill="none"/></svg></div>
<svg class="abs" style="left:0;top:600px" width="1200" height="300" viewBox="0 600 1200 300">
  <defs><linearGradient id="arcGrad" x1="0" x2="1"><stop offset="0" stop-color="#a95bdc"/><stop offset="1" stop-color="#3f9cf0"/></linearGradient></defs>
  <path d="M0 660 Q560 1030 1200 630 L1200 900 L0 900 Z" fill="#000"/>
  <path d="M0 660 Q560 1030 1200 630" stroke="url(#arcGrad)" stroke-width="9" fill="none"/>
</svg>

<!-- product listings -->
<h2 class="abs sec-title display" style="top:950px">PRODUCT LISTINGS</h2>
<div class="abs bar" style="left:575px;top:1010px;width:50px"></div>

<div class="abs cat" style="left:113px;top:1059px">
  <div class="cat-ring"><div class="cat-photo" role="img" aria-label="Lit aromatherapy candles with reed diffuser" style="background:linear-gradient(160deg,#6b5440,#d9b98a 50%,#3a2e26)"></div></div>
  <div class="cat-icon"><svg width="34" height="34" viewBox="0 0 34 34"><path d="M17 2c3 4 3 6 0 8-3-2-3-4 0-8z" fill="#fff"/><rect x="12" y="12" width="10" height="12" fill="#fff"/><rect x="5" y="26" width="24" height="5" fill="#fff"/></svg></div>
  <div class="cat-name">AROMATHERAPY<br>CANDLES</div>
</div>
<div class="abs cat" style="left:364px;top:1059px">
  <div class="cat-ring"><div class="cat-photo" role="img" aria-label="Lotion bottle among lavender and green leaves" style="background:linear-gradient(160deg,#b9b7a6,#efe9dc 50%,#8d9a77)"></div></div>
  <div class="cat-icon"><svg width="30" height="34" viewBox="0 0 30 34"><rect x="11" y="2" width="8" height="5" fill="#fff"/><rect x="6" y="9" width="18" height="23" rx="3" fill="#fff"/><path d="M6 18l18 6" stroke="#8a5fe6" stroke-width="2"/></svg></div>
  <div class="cat-name">LOTIONS</div>
</div>
<div class="abs cat" style="left:614px;top:1059px">
  <div class="cat-ring"><div class="cat-photo" role="img" aria-label="Green herbal soap bar" style="background:linear-gradient(160deg,#cfd8cf,#8bb58a 55%,#e3e6e0)"></div></div>
  <div class="cat-icon"><svg width="34" height="32" viewBox="0 0 34 32"><circle cx="9" cy="6" r="4" stroke="#fff" stroke-width="2" fill="none"/><circle cx="18" cy="4" r="2.5" stroke="#fff" stroke-width="2" fill="none"/><rect x="4" y="13" width="26" height="15" rx="6" stroke="#fff" stroke-width="3" fill="none" transform="rotate(-12 17 20)"/></svg></div>
  <div class="cat-name" style="color:#3aa8e8;text-decoration:underline">SOAPS</div>
</div>
<div class="abs cat" style="left:865px;top:1059px">
  <div class="cat-ring"><div class="cat-photo" role="img" aria-label="Body spray bottle with sliced lemon and herbs" style="background:linear-gradient(160deg,#e2e5e1,#d8c884 50%,#6c7a55)"></div></div>
  <div class="cat-icon"><svg width="20" height="34" viewBox="0 0 20 34"><rect x="7" y="1" width="6" height="5" fill="#fff"/><rect x="3" y="8" width="14" height="24" rx="3" fill="#fff"/></svg></div>
  <div class="cat-name">BODY SPRAYS</div>
</div>
<div class="abs dots" style="left:548px;top:1410px"><span></span><span class="on"></span><span></span><span></span></div>

<!-- featured products -->
<section class="abs featured"></section>
<div class="abs feat-photo" role="img" aria-label="Woman holding an amber dropper bottle among green foliage"></div>
<div class="abs dots" style="left:178px;top:2060px"><span class="on"></span><span></span><span></span></div>
<h2 class="abs display" style="left:419px;top:1620px;font-size:46px">FEATURED PRODUCTS</h2>
<div class="abs bar" style="left:421px;top:1682px;width:55px;margin:0"></div>
<div class="abs nav-pair" style="left:1009px;top:1631px;display:flex;gap:8px">
  <div class="l"><svg width="8" height="12" viewBox="0 0 8 12"><path d="M6 1L1 6l5 5" stroke="#fff" stroke-width="2" fill="none"/></svg></div>
  <div class="r"><svg width="8" height="12" viewBox="0 0 8 12"><path d="M2 1l5 5-5 5" stroke="#fff" stroke-width="2" fill="none"/></svg></div>
</div>
<div class="abs tab on" style="left:421px;top:1719px;width:109px">LOTIONS <span class="chev"></span></div>
<div class="abs tab" style="left:537px;top:1719px;width:109px">CANDLES <span class="chev"></span></div>
<div class="abs tab" style="left:654px;top:1719px;width:109px">SOAPS <span class="chev"></span></div>
<div class="abs tab" style="left:770px;top:1719px;width:133px">BODY SPRAYS <span class="chev"></span></div>
<div class="abs tab" style="left:912px;top:1719px;width:125px">WAX MELTS <span class="chev"></span></div>

<div class="abs pcard" style="left:421px;top:1810px;width:207px;height:302px">
  <div class="ph" role="img" aria-label="Green lotion bottle with lavender" style="background:linear-gradient(160deg,#6fae6a,#e3efe0 60%,#8f86b0)"></div><div class="cart"></div>
  <h3>LOREM IPSUM DOL</h3><div class="rating"><b>★★★★★</b> 1 review</div><div class="price">$950.00</div>
</div>
<div class="abs pcard hl" style="left:649px;top:1810px;width:211px;height:302px">
  <div class="ph" role="img" aria-label="Amber oil bottles and cream jars in sunlight" style="background:linear-gradient(160deg,#efe4d2,#d9a95a 55%,#f3ebe0)"></div><div class="cart"></div>
  <h3>LOREM IPSUM DOL</h3><div class="rating"><b>★★★★★</b> 1 review</div><div class="price">$950.00</div>
</div>
<div class="abs pcard" style="left:880px;top:1810px;width:208px;height:302px">
  <div class="ph" role="img" aria-label="Golden body spray among white flowers" style="background:linear-gradient(160deg,#5d6d4c,#efe8d4 50%,#d4c48a)"></div><div class="cart"></div>
  <h3>LOREM IPSUM DOL</h3><div class="rating"><b>★★★★★</b> 1 review</div><div class="price">$950.00</div>
</div>

<!-- testimonials -->
<section class="abs clients" role="img" aria-label="Person in meditation pose with essential oil bottle and dried flowers"></section>
<h2 class="abs sec-title display" style="top:2276px;color:#111">WHAT OUR CLIENTS SAY</h2>
<div class="abs bar" style="left:575px;top:2336px;width:50px"></div>
<div class="abs" style="left:25px;top:2524px;width:65px;height:20px;border-radius:10px;background:linear-gradient(90deg,#a95bdc,#5a8ef0)"></div>
<svg class="abs" style="left:25px;top:2524px" width="45" height="20" viewBox="0 0 45 20"><path d="M44 10H4M11 3L3 10l8 7" stroke="#111" stroke-width="2.5" fill="none"/></svg>
<div class="abs" style="left:778px;top:2524px;width:62px;height:20px;border-radius:10px;background:linear-gradient(90deg,#a95bdc,#5a8ef0)"></div>
<svg class="abs" style="left:797px;top:2524px" width="45" height="20" viewBox="0 0 45 20"><path d="M1 10h40M34 3l8 7-8 7" stroke="#111" stroke-width="2.5" fill="none"/></svg>

<div class="abs tcard" style="left:112px;top:2392px">
  <span class="qmark">“</span>
  <p>Sed ut perspiciatis unde omnis iste natus error sit voluptatem accusantium doloremque laudantium, totam rem aperiam, eaque ipsa quae ab illo inventore veritatis et quasi architecto be atae vitae dicta explicabo.</p>
  <div class="person"><div class="avatar" role="img" aria-label="Client portrait"></div><div><b>MAREN TOLLIVER</b><i>★★★★★</i></div></div>
</div>
<div class="abs tcard" style="left:446px;top:2392px">
  <span class="qmark">“</span>
  <p>Sed ut perspiciatis unde omnis iste natus error sit voluptatem accusantium doloremque laudantium, totam rem aperiam, eaque ipsa quae ab illo inventore veritatis et quasi architecto be atae vitae dicta explicabo.</p>
  <div class="person"><div class="avatar" role="img" aria-label="Client portrait" style="background:linear-gradient(160deg,#e5e1dc,#7c8a9a)"></div><div><b>DORIAN PELL</b><i>★★★★★</i></div></div>
</div>

<!-- best sellers -->
<h2 class="abs sec-title display" style="top:2824px">BEST SELLERS</h2>
<div class="abs bar" style="left:575px;top:2884px;width:50px"></div>
<div class="abs nav-pair" style="left:1009px;top:2836px;display:flex;gap:8px">
  <div class="l"><svg width="8" height="12" viewBox="0 0 8 12"><path d="M6 1L1 6l5 5" stroke="#fff" stroke-width="2" fill="none"/></svg></div>
  <div class="r"><svg width="8" height="12" viewBox="0 0 8 12"><path d="M2 1l5 5-5 5" stroke="#fff" stroke-width="2" fill="none"/></svg></div>
</div>
<div class="abs pcard" style="left:112px;top:2936px;width:222px;height:301px">
  <div class="ph" role="img" aria-label="Teal serum bottle with white blossoms" style="background:linear-gradient(160deg,#1d8fb0,#8fd3d6 55%,#6a5a45)"></div><div class="cart"></div>
  <h3>LOREM IPSUM DOL</h3><div class="rating"><b>★★★★★</b> 1 review</div><div class="price">$950.00</div>
</div>
<div class="abs pcard" style="left:363px;top:2936px;width:222px;height:301px">
  <div class="ph" role="img" aria-label="Amber dropper bottles on white surface" style="background:linear-gradient(160deg,#eeeeec,#cfcfcb 50%,#6e4a2e)"></div><div class="cart"></div>
  <h3>LOREM IPSUM DOL</h3><div class="rating"><b>★★★★★</b> 1 review</div><div class="price">$950.00</div>
</div>
<div class="abs pcard hl" style="left:611px;top:2936px;width:228px;height:301px">
  <div class="ph" role="img" aria-label="Handmade olive soap bars on wood" style="background:linear-gradient(160deg,#3b2a1c,#b9ad7a 50%,#5a3f26)"></div><div class="cart"></div>
  <h3>LOREM IPSUM DOL</h3><div class="rating"><b>★★★★★</b> 1 review</div><div class="price">$950.00</div>
</div>
<div class="abs pcard" style="left:864px;top:2936px;width:224px;height:301px">
  <div class="ph" role="img" aria-label="Lit candle in a bowl with bokeh lights" style="background:linear-gradient(160deg,#2a2a22,#e9d8b5 55%,#4a4a42)"></div><div class="cart"></div>
  <h3>LOREM IPSUM DOL</h3><div class="rating"><b>★★★★★</b> 1 review</div><div class="price">$950.00</div>
</div>

<!-- footer -->
<svg class="abs" style="left:0;top:3320px" width="1200" height="240" viewBox="0 3320 1200 240">
  <defs><linearGradient id="footArc" x1="0" x2="1"><stop offset="0" stop-color="#a95bdc"/><stop offset="1" stop-color="#3f9cf0"/></linearGradient></defs>
  <path d="M0 3542 Q600 3140 1200 3542 L1200 3560 L0 3560Z" fill="#0b0b0b"/>
  <path d="M0 3542 Q600 3140 1200 3542" stroke="url(#footArc)" stroke-width="9" fill="none"/>
</svg>
<div class="abs" style="left:0;top:3560px;width:1200px;height:285px;background:#0b0b0b"></div>

<div class="abs" style="left:112px;top:3630px;display:flex;align-items:center;gap:6px"><span class="wordmark-dot"></span><span class="wordmark">VELQUINT</span></div>

<div class="abs fhead" style="left:336px;top:3506px">OTHER LINKS</div>
<div class="abs flink" style="left:336px;top:3548px"><span class="fchev"></span>Home</div>
<div class="abs flink" style="left:336px;top:3593px"><span class="fchev"></span>About Us</div>
<div class="abs flink" style="left:336px;top:3637px"><span class="fchev"></span>Products</div>
<div class="abs flink" style="left:336px;top:3682px"><span class="fchev"></span>Blog</div>
<div class="abs flink" style="left:336px;top:3726px"><span class="fchev"></span>Contact Us</div>

<div class="abs fhead" style="left:518px;top:3506px">CONTACT US</div>
<div class="abs cicon" style="left:518px;top:3549px"><svg width="12" height="16" viewBox="0 0 12 16"><path d="M6 0a6 6 0 016 6c0 4-6 10-6 10S0 10 0 6a6 6 0 016-6z" fill="#9a58dc"/><circle cx="6" cy="6" r="2" fill="#fff"/></svg></div>
<div class="abs" style="left:572px;top:3550px;font-size:14px;line-height:19px">123 Lorem Ipsum Dolore Sed,<br>United States</div>
<div class="abs cicon" style="left:518px;top:3600px"><svg width="14" height="11" viewBox="0 0 14 11"><rect width="14" height="11" rx="1.5" fill="#9a58dc"/><path d="M1 1l6 5 6-5" stroke="#fff" stroke-width="1.4" fill="none"/></svg></div>
<div class="abs" style="left:572px;top:3611px;font-size:14px">info@velquint.com</div>
<div class="abs cicon" style="left:518px;top:3651px"><svg width="14" height="14" viewBox="0 0 14 14"><path d="M3 0l3 3-2 2c1 2 3 4 5 5l2-2 3 3-2 3C6 14 0 8 0 2z" fill="#9a58dc"/></svg></div>
<div class="abs" style="left:572px;top:3662px;font-size:14px">+1 (555) 014 2270</div>

<div class="abs fhead" style="left:800px;top:3506px">SIGN UP TO OUR NEWSLETTER</div>
<div class="abs" style="left:800px;top:3549px;font-size:13px">Email</div>
<div class="abs" style="left:800px;top:3576px;width:287px;height:2px;background:#fff"></div>
<div class="abs btn" style="left:801px;top:3594px;width:133px;height:46px;font-size:15px">SUBSCRIBE</div>
<div class="abs fsoc" style="left:801px;top:3664px" aria-label="Social link"></div>
<div class="abs fsoc" style="left:844px;top:3664px" aria-label="Social link"></div>
<div class="abs fsoc" style="left:886px;top:3664px" aria-label="Social link"></div>
<div class="abs fsoc" style="left:930px;top:3664px" aria-label="Social link"></div>

<div class="abs" style="left:112px;top:3776px;width:976px;height:1px;background:#333"></div>
<div class="abs" style="left:0;width:1200px;top:3798px;text-align:center;font-size:13px">© 2025 VELQUINT &nbsp;| &nbsp;All Rights Reserved</div>
<div class="abs" style="left:1030px;top:3792px;font-size:22px;font-weight:700;color:#6a74f0">vonk</div>

</body>
</html>
```